A private security company called "Tavron Security Services Ltd"

Hello everybody,

We need a web page for a company based in NZ. It is mainly an informative website so it would be wonderful if the designer puts their absolute best into making it a website that I would really appreciate. The website needs to show professionalism and also needs to make our web surfers find the information they need in a click. the company's colour is black and silver, and if those two colours could be integrated into the website it would be absolutely lovely. Please do contact me for any information.

Sincerely,
Dorian Vaskel

Industry/Entity Type

Security

```html
<!DOCTYPE html>
<html lang="en">
<head>
<meta charset="utf-8">
<title>Tavron Security Services Ltd</title>
<link rel="stylesheet" href="https://fonts.googleapis.com/css2?family=Open+Sans:wght@300;400;600;700&display=swap">
<style>
:root{
  --night:#1b2a33;
  --night-deep:#121d24;
  --card:#1a2327;
  --ink:#1e1e1e;
  --muted:#8a8f93;
  --silver:#e9e9e9;
  --silver-line:#c9c9c9;
  --gold:#f0b85a;
  --footer:#050505;
  --footer-text:#a9a9a9;
  --white:#ffffff;
}
*{box-sizing:border-box;margin:0;padding:0}
html,body{width:822px;height:1200px;overflow:hidden}
body{position:relative;background:var(--white);font-family:"Open Sans",Arial,sans-serif;color:var(--ink)}
.abs{position:absolute}

/* header */
.masthead{left:0;top:0;width:822px;height:557px;background:radial-gradient(ellipse at 50% 0%,#243540 0%,var(--night) 45%,var(--night-deep) 100%)}
.brand{left:76px;top:30px;width:120px;color:var(--white);text-align:center}
.brand-mark{display:block;width:22px;height:22px;border-radius:50%;background:var(--silver);margin:0 auto 6px}
.brand-name{font-size:17px;font-weight:700;letter-spacing:2px;line-height:1}
.brand-sub{font-size:8px;font-weight:700;letter-spacing:.4px;margin-top:3px;line-height:1}
.callout{right:75px;top:34px;color:var(--gold);font-size:16px;font-weight:400}
.callout b{font-weight:700}
.search{left:593px;top:61px;width:153px;height:22px;background:#101a20;color:#b9c0c4;font-size:9.5px;padding:5px 8px}
.search svg{position:absolute;right:7px;top:5px}

.nav{left:75px;top:113px;width:672px;height:29px;background:linear-gradient(#ffffff,#e6e6e6);border-radius:3px;display:flex;font-size:9.6px;color:#222}
.nav a{color:inherit;text-decoration:none;display:flex;align-items:center;justify-content:center;border-right:1px solid #cfcfcf}
.nav a:last-child{border-right:0}

.hero{left:75px;top:151px;width:672px;height:383px;border-radius:4px;overflow:hidden;background:linear-gradient(180deg,#7c94ae 0%,#b7b0a6 42%,#d08b4a 62%,#5b4a3c 78%,#3b3029 100%)}
.hero-panel{left:0;top:113px;width:368px;height:144px;background:rgba(25,30,38,.72)}
.hero-title{left:17px;top:18px;color:var(--white);font-size:19px;font-weight:700;white-space:nowrap}
.hero-title span{font-weight:400;margin-left:6px}
.hero-copy{left:17px;top:52px;width:340px;color:var(--white);font-size:8.2px;line-height:12.5px}
.btn-more{left:16px;top:101px;width:86px;height:27px;background:#f7f2ea;border-radius:2px;font-size:9.5px;font-weight:600;display:flex;align-items:center;justify-content:center;color:#222}
.dots{right:20px;top:369px;display:flex;gap:3px}
.dots i{width:6px;height:6px;border-radius:50%;background:var(--white)}
.dots i.on{background:var(--gold)}

/* intro */
.welcome-title{left:76px;top:596px;font-size:19.5px;font-weight:300;letter-spacing:-.3px}
.welcome-title b{font-weight:700}
.welcome-photo{left:76px;top:629px;width:124px;height:92px;background:linear-gradient(180deg,#bcc4cf 0%,#8c98a6 55%,#4c5561 100%)}
.welcome-copy{left:209px;top:638px;width:256px;font-size:8.5px;line-height:11px;color:#333}
.read-link{left:210px;top:703px;font-size:8.5px;color:#666;text-decoration:underline}
.divider{left:496px;top:592px;width:1px;height:160px;background:linear-gradient(transparent,#dcdcdc,transparent)}
.contact-title{left:518px;top:596px;font-size:19.5px;font-weight:300}
.field{height:19px;background:linear-gradient(#e2e2e2,#f2f2f2);border:1px solid #d2d2d2;font-size:8px;color:#999;padding:4px 6px}
.send{left:663px;top:676px;width:83px;height:19px;background:#0c1418;color:var(--white);font-size:8.5px;font-weight:600;display:flex;align-items:center;justify-content:center;letter-spacing:.3px}
.shade{left:90px;top:752px;width:642px;height:8px;background:radial-gradient(ellipse at 50% 0%,rgba(0,0,0,.08),transparent 70%)}

/* services */
.service{top:777px;width:145px;height:215px;background:var(--card);color:var(--white);text-align:center}
.service svg{position:absolute;left:50%;transform:translateX(-50%);top:25px}
.service h3{position:absolute;left:0;right:0;top:82px;font-size:10.8px;font-weight:600;letter-spacing:.1px}
.service p{position:absolute;left:14px;right:14px;top:109px;font-size:7.4px;line-height:10.3px;color:#7d8589}

/* footer */
.footer{left:0;top:1019px;width:822px;height:181px;background:var(--footer);color:var(--footer-text)}
.foot-head{color:var(--white);font-size:10.2px;top:21px}
.foot-rule{top:39px;height:1px;background:#1e1e1e}
.foot-text{font-size:9px;line-height:13.7px;font-weight:300}
.socials{left:294px;top:76px;display:flex;gap:4px}
.socials span{width:16px;height:16px;border-radius:2px}
.sub-input{left:560px;top:104px;width:114px;height:24px;background:var(--white);color:#aaa;font-size:9px;padding:6px 7px}
.sub-ok{left:674px;top:104px;width:34px;height:24px;background:#111;border:1px solid #555;color:var(--white);font-size:10px;display:flex;align-items:center;justify-content:center}
.legal{left:0;width:822px;top:160px;text-align:center;font-size:8.5px;color:#ddd}
</style>
</head>
<body>

<header class="abs masthead">
  <div class="abs brand"><span class="brand-mark"></span><div class="brand-name">TAVRON</div><div class="brand-sub">SECURITY SERVICES LTD.</div></div>
  <div class="abs callout">Call: <b>418 2206 731</b></div>
  <div class="abs search">Search
    <svg width="12" height="12" viewBox="0 0 12 12"><circle cx="5" cy="5" r="3.8" fill="none" stroke="#aab2b6" stroke-width="1.5"/><line x1="8" y1="8" x2="11" y2="11" stroke="#aab2b6" stroke-width="1.6"/></svg>
  </div>
  <nav class="abs nav">
    <a style="width:70px">Home</a>
    <a style="width:96px">About Us</a>
    <a style="width:130px">Security System</a>
    <a style="width:150px">Specialized Security</a>
    <a style="width:97px">Carreers</a>
    <a style="width:129px">Contact Us</a>
  </nav>
  <section class="abs hero" role="img" aria-label="Dome security camera on a glass building balcony at sunset over the city">
    <div class="abs hero-panel">
      <h1 class="abs hero-title">Newzealand’s Best<span>Security Company</span></h1>
      <p class="abs hero-copy">It is a long established fact that a reader will be distracted by the readable content of a page when looking at its layout. The point of using Lorem Ipsum is that it has a more-or-less normal distribution of letters</p>
      <div class="abs btn-more">READ MORE</div>
    </div>
    <div class="abs dots"><i></i><i class="on"></i><i></i><i></i></div>
  </section>
</header>

<h2 class="abs welcome-title">Welcome to <b>best Perosonal Guard Security</b></h2>
<div class="abs welcome-photo" role="img" aria-label="Row of security cameras on poles before city towers"></div>
<p class="abs welcome-copy">It is a long established fact that a reader will be distracted by the readable content of a page when looking at its layout. The point of using Lorem Ipsum is that it has a more-or-less normal distribution of letters, as opposed to using 'Content here, content here', making it look like readable English.</p>
<a class="abs read-link">Read More</a>
<div class="abs divider"></div>

<h2 class="abs contact-title">Contact Us</h2>
<div class="abs field" style="left:517px;top:630px;width:112px">Your Name*</div>
<div class="abs field" style="left:633px;top:630px;width:113px">Email*</div>
<div class="abs field" style="left:517px;top:652px;width:112px">Contact Phone #</div>
<div class="abs field" style="left:633px;top:652px;width:113px">Intrested in*</div>
<div class="abs field" style="left:517px;top:676px;width:142px">Comments</div>
<div class="abs send">SEND NOW</div>
<div class="abs shade"></div>

<article class="abs service" style="left:75px">
  <svg width="40" height="34" viewBox="0 0 40 34" fill="var(--silver)"><path d="M4 12 L28 2 L33 12 L9 22 Z"/><rect x="26" y="14" width="4" height="10"/><rect x="26" y="22" width="12" height="4"/><path d="M34 10 h4 v12 h-4z"/><path d="M10 22 l-6 6 l3 2 l6-6z"/></svg>
  <h3>SECURITY CAMERAS</h3>
  <p style="top:112px">It is a long established fact that a reader will be distracted by the readable content of a page when look-ing at its layout. The point of using Lorem Ipsum is that it has a more-or-less normal distribution of letters</p>
</article>
<article class="abs service" style="left:250px">
  <svg width="36" height="34" viewBox="0 0 36 34" fill="none" stroke="var(--silver)" stroke-width="2.4"><path d="M6 4 L22 4 L26 14 L10 22 Z"/><rect x="18" y="16" width="16" height="14" rx="2"/><circle cx="26" cy="23" r="3"/><path d="M4 24 L10 30"/></svg>
  <h3>CCTV CAMERAS</h3>
  <p>It is a long established fact that a reader will be distracted by the readable content of a page when look-ing at its layout. The point of using Lorem Ipsum is that it has a more-or-less normal distribution of letters</p>
</article>
<article class="abs service" style="left:425px">
  <svg width="32" height="34" viewBox="0 0 32 34"><path d="M16 2 L30 7 C30 20 24 28 16 32 C8 28 2 20 2 7 Z" fill="var(--silver)"/><path d="M16 7 L25 10 C25 19 21 24 16 27 Z" fill="var(--card)"/></svg>
  <h3>SECURITY</h3>
  <p>It is a long established fact that a reader will be distracted by the readable content of a page when look-ing at its layout. The point of using Lorem Ipsum is that it has a more-or-less normal distribution of letters</p>
</article>
<article class="abs service" style="left:602px">
  <svg width="34" height="34" viewBox="0 0 34 34"><path d="M14 2 L26 6 C26 18 21 26 14 30 C7 26 2 18 2 6 Z" fill="none" stroke="var(--silver)" stroke-width="2.6"/><circle cx="24" cy="24" r="8" fill="var(--silver)"/><path d="M20 24 l3 3 l5-6" fill="none" stroke="var(--card)" stroke-width="2"/></svg>
  <h3>PEROSNAL SECURITY</h3>
  <p>It is a long established fact that a reader will be distracted by the readable content of a page when look-ing at its layout. The point of using Lorem Ipsum is that it has a more-or-less normal distribution of letters</p>
</article>

<footer class="abs footer">
  <h4 class="abs foot-head" style="left:86px">CONTACT US</h4>
  <div class="abs foot-rule" style="left:86px;width:160px"></div>
  <p class="abs foot-text" style="left:88px;top:56px">Newzealand, Auckland 1010<br>27 Harbour Lane<br>phone: +64 09 412 7785<br>Fax: +64 09 412 7786<br>Email: office@tavronsecure.nz</p>

  <h4 class="abs foot-head" style="left:294px">GO SOCIAL</h4>
  <div class="abs foot-rule" style="left:294px;width:160px"></div>
  <p class="abs foot-text" style="left:294px;top:56px">Stay in touch with us:</p>
  <div class="abs socials" aria-label="Social links">
    <span style="background:#3b5a9a"></span><span style="background:#2ea3d9"></span><span style="background:#d2412f"></span><span style="background:#c8232c"></span><span style="background:#6b4f3d"></span><span style="background:#f08a24"></span>
  </div>

  <h4 class="abs foot-head" style="left:560px">SUBSCRIBE</h4>
  <div class="abs foot-rule" style="left:560px;width:160px"></div>
  <p class="abs foot-text" style="left:560px;top:56px;width:200px">Enter your e-mail below to subscribe to our free newsletter.<br>We promise not to bother you often!</p>
  <div class="abs sub-input">Enter Email</div>
  <div class="abs sub-ok">OK</div>

  <div class="abs foot-rule" style="left:88px;width:646px;top:149px"></div>
  <p class="abs legal">© Tavron Security Services 2014. Privacy Policy | Terms of Service</p>
</footer>

</body>
</html>
```